Marlow Estate Fixers (Handyman / Home Improvement Company)

Looking for a double sided professional looking business card with Logo attached to be highlighted on one side and throwing in an image of a handyman as an option would be nice to see as well. We are a company focused on providing quality Handyman and Home improvement services in a timely manner that is done right the first time with integrity

Industry/Entity Type

Handyman / Home Improvement

Contact Information for Business Card

(LOGO, Name, Mobile and office phone numbers, email) on front side of card, (the words "The SOLUTION to all of your Handyman and Home Improvement needs" followed by "Family Owned and Operated" at the very bottom) on the back.

Colors
EB3D1F
EC4F4E
F09395
F8D3D4
FCEDEE

Requirements
Must have
• Red, Gray, Black Color scheme
Should not have
• No Yellow or Blue colors

```html
<!DOCTYPE html>
<html lang="en">
<head>
<meta charset="utf-8">
<title>Marlow Estate Fixers – Business Card</title>
<link href="https://fonts.googleapis.com/css2?family=Michroma&family=Poppins:wght@400;600&display=swap" rel="stylesheet">
<style>
  :root {
    --page: #e7e8ea;
    --card: #050709;
    --red: #e8252b;
    --red-soft: #f09395;
    --pink: #f8d3d4;
    --white: #f4f4f4;
    --gray: #bdbdbd;
    --tan: #8a6a45;
  }
  html, body { margin: 0; padding: 0; overflow: hidden; }
  body {
    width: 1194px; height: 1200px;
    background: var(--page);
    position: relative;
    font-family: "Poppins", sans-serif;
  }
  .card {
    position: absolute;
    left: 307px;
    width: 579px; height: 331px;
    background: var(--card);
    overflow: hidden;
  }
  .card--front { top: 166px; }
  .card--back { top: 638px; }

  .card__band { position: absolute; left: 0; bottom: 0; width: 579px; height: 19px; display: block; }

  /* front */
  .hero-art {
    position: absolute; left: 6px; top: 17px; width: 295px; height: 280px;
    border-radius: 40px 40px 6px 6px;
    background: linear-gradient(160deg, #b8913a 0%, #c2262b 45%, #d9b07a 80%, #8a6a45 100%);
  }
  .brand {
    position: absolute; right: 30px; top: 52px;
    display: flex; align-items: center; gap: 8px;
    font-family: "Michroma", sans-serif; font-size: 11px; color: var(--white);
    letter-spacing: 0.5px; text-transform: uppercase;
  }
  .brand__dot { width: 14px; height: 14px; border-radius: 50%; background: var(--red); }
  .person__name {
    position: absolute; right: 33px; top: 137px; margin: 0;
    font-family: "Michroma", sans-serif; font-size: 18.5px; color: var(--red);
    letter-spacing: 2px; font-weight: 400;
  }
  .person__role {
    position: absolute; right: 33px; top: 162px; margin: 0;
    font-size: 13px; color: var(--white); letter-spacing: 2.5px;
  }
  .person__rule { position: absolute; left: 273px; top: 175px; width: 191px; height: 1.5px; background: var(--gray); }
  .contact { position: absolute; right: 33px; top: 205px; margin: 0; padding: 0; list-style: none; }
  .contact li {
    display: flex; justify-content: flex-end; align-items: center; gap: 14px;
    font-size: 12px; color: var(--white); letter-spacing: 0.6px;
    height: 29px;
  }
  .contact svg { width: 17px; height: 17px; }

  /* back */
  .hero-art--faded {
    left: 236px; top: 4px; width: 343px; height: 307px;
    opacity: 0.35; border-radius: 60px 60px 0 0;
  }
  .brand--center {
    right: auto; left: 0; width: 579px; top: 108px; justify-content: center;
    font-size: 14px;
  }
  .brand--center .brand__dot { width: 18px; height: 18px; }
  .tagline {
    position: absolute; left: 0; width: 579px; top: 226px; margin: 0;
    text-align: center; font-family: "Michroma", sans-serif; font-size: 13px;
    line-height: 19px; color: var(--white); letter-spacing: 0.5px;
  }
  .motto {
    position: absolute; left: 0; width: 579px; top: 284px; margin: 0;
    text-align: center; font-size: 12.5px; font-weight: 600; color: var(--red);
  }
</style>
</head>
<body>
  <svg width="0" height="0" style="position:absolute">
    <defs>
      <linearGradient id="band-fade" x1="0" x2="1" y1="0" y2="0">
        <stop offset="0" stop-color="#fcedee"/>
        <stop offset="0.55" stop-color="#f09395"/>
        <stop offset="1" stop-color="#e8252b"/>
      </linearGradient>
    </defs>
  </svg>

  <section class="card card--front">
    <div class="hero-art" role="img" aria-label="Illustration of a bearded handyman in a hard hat and red shirt holding a sledgehammer"></div>
    <div class="brand"><span class="brand__dot"></span><span>Marlow Estate Fixers</span></div>
    <h1 class="person__name">DALE HARROW</h1>
    <p class="person__role">OWNER</p>
    <div class="person__rule"></div>
    <ul class="contact">
      <li>(555) 304-8126
        <svg viewBox="0 0 20 20" fill="none" stroke="#e8252b" stroke-width="1.3"><circle cx="10" cy="10" r="8.5"/><path d="M7 6.2l1.4-.4 1 2.2-1 .8c.5 1.1 1.3 1.9 2.4 2.4l.8-1 2.2 1-.4 1.4c-3.2.3-6.7-3.2-6.4-6.4z"/></svg>
      </li>
      <li>(555) 304-8127
        <svg viewBox="0 0 20 20" fill="none" stroke="#e8252b" stroke-width="1.3"><circle cx="10" cy="10" r="8.5"/><rect x="7.3" y="5" width="5.4" height="10" rx="1"/></svg>
      </li>
      <li>daleharrow@mail.com
        <svg viewBox="0 0 20 20" fill="none" stroke="#e8252b" stroke-width="1.3"><circle cx="10" cy="10" r="8.5"/><rect x="5.5" y="7" width="9" height="6.5"/><path d="M5.5 7l4.5 3.5L14.5 7"/></svg>
      </li>
    </ul>
    <svg class="card__band" viewBox="0 0 579 19" preserveAspectRatio="none">
      <rect width="579" height="19" fill="url(#band-fade)"/>
      <rect x="0" y="12" width="312" height="7" fill="#ffffff"/>
      <path d="M0 7 H318 L325 0 H330 L318 12 H0 Z" fill="#050709"/>
    </svg>
  </section>

  <section class="card card--back">
    <div class="hero-art hero-art--faded" role="img" aria-label="Faded illustration of the handyman with a sledgehammer"></div>
    <div class="brand brand--center"><span class="brand__dot"></span><span>Marlow Estate Fixers</span></div>
    <p class="tagline">YOUR SOLUTION TO ALL OF YOUR HANDYMAN<br>AND HOME IMPROVEMENT NEEDS</p>
    <p class="motto">Family Owned and Operated</p>
    <svg class="card__band" viewBox="0 0 579 19" preserveAspectRatio="none">
      <rect width="579" height="19" fill="url(#band-fade)"/>
      <rect x="0" y="12" width="312" height="7" fill="#ffffff"/>
      <path d="M0 7 H318 L325 0 H330 L318 12 H0 Z" fill="#050709"/>
    </svg>
  </section>
</body>
</html>
```